R7M Horizon Business Card Design

We need a business card created for our New Business "R7M Horizon"<br/><br/>The business card design is up to you however the following information must be on the business card:<br/><br/>Front of the business card -<br/>Email :darrenp@r7mhorizon.nz<br/>Mobile: +64 (0) 22 4870 619<br/>Website: www.r7mhorizon.nz<br/>Card Owner Name: Darren Paltrow<br/>Company Title: Business Development Manager<br/>Slogan: "The BEST of both worlds". <br/>Logo On the front attached to the design brief<br/><br/>On the back: <br/>Space on the back for 4 more versions of the logo across the bottom of the card indicating different subsidiary brands - R7M Coffee, R7M Arts, R7M ?? (The card will be used for all of these brands - We Will add the extra subsidiary logos to the design once the design is finished (We are a graphics design team). <br/><br/>Other than that we want a premium feeling logo that remains universally usable depending on the business entity that we are using the card for. The use of bright bold colours would be great but we still want the card to feel premium.
Target Market(s)
Gift Design and Manufacturing Companies
Contact Information for Business Card
Front of the business card -
Email :darrenp@r7mhorizon.nz
Mobile: +64 (0) 22 4870 619
Website: www.r7mhorizon.nz
Card Owner Name: Darren Paltrow
Company Title: Business Development Manager
Slogan: "The BEST of both worlds".
Logo On the front attached to the design brief

```html
<!DOCTYPE html>
<html lang="en">
<head>
<meta charset="utf-8">
<title>R7M Horizon Business Card</title>
<link href="https://fonts.googleapis.com/css2?family=Montserrat:wght@500;600;700&family=Open+Sans:wght@400;600&display=swap" rel="stylesheet">
<style>
  :root {
    --brand-blue: #3548a0;
    --ink: #2b2b2b;
    --paper: #ffffff;
    --backdrop: #e6e7ea;
  }
  * { box-sizing: border-box; margin: 0; padding: 0; }
  html, body {
    width: 1200px; height: 1015px; overflow: hidden;
    background: var(--backdrop);
  }
  .sheet {
    position: relative; width: 1200px; height: 1015px;
  }
  .card {
    position: absolute; left: 260px; width: 680px; height: 390px;
    overflow: hidden;
    box-shadow: 0 6px 18px rgba(0,0,0,0.15);
  }
  .card--back { top: 90px; background: var(--brand-blue); }
  .card--front { top: 535px; background: var(--paper); }

  .wordmark {
    position: absolute; display: flex; align-items: center; gap: 14px;
    font-family: "Montserrat", sans-serif; font-weight: 700;
    letter-spacing: 0.5px; white-space: nowrap;
  }
  .wordmark__dot { border-radius: 50%; flex: none; }
  .card--back .wordmark {
    left: 50%; top: 50%; transform: translate(-50%, -50%);
    color: var(--paper); font-size: 48px;
  }
  .card--back .wordmark__dot { width: 56px; height: 56px; border: 6px solid var(--paper); }
  .card--front .wordmark {
    right: 44px; top: 62px; color: var(--brand-blue); font-size: 34px;
  }
  .card--front .wordmark__dot { width: 42px; height: 42px; border: 5px solid var(--brand-blue); }

  .owner {
    position: absolute; left: 48px; top: 222px;
  }
  .owner__name {
    font-family: "Montserrat", sans-serif; font-weight: 700;
    font-size: 21px; color: var(--brand-blue); text-transform: uppercase;
    letter-spacing: 0.3px;
  }
  .owner__title {
    font-family: "Open Sans", sans-serif; font-size: 16px; color: var(--ink);
    margin-top: 1px;
  }
  .contacts {
    position: absolute; left: 48px; top: 300px; list-style: none;
    font-family: "Open Sans", sans-serif; font-size: 16px; color: var(--ink);
  }
  .contacts li { display: flex; align-items: center; gap: 8px; height: 22px; }
  .contacts svg { width: 18px; height: 18px; flex: none; }
  .contacts .domain { color: var(--brand-blue); }

  .slogan {
    position: absolute; right: 34px; top: 286px;
    font-family: "Montserrat", sans-serif; font-weight: 500;
    font-size: 17px; color: var(--ink); text-transform: uppercase;
    letter-spacing: -0.2px;
  }
  .rule-thin {
    position: absolute; right: 0; top: 272px; width: 160px; height: 4px;
    background: var(--brand-blue);
  }
  .rule-band {
    position: absolute; right: 0; top: 326px; width: 255px; height: 12px;
    background: var(--brand-blue);
  }
</style>
</head>
<body>
<main class="sheet">
  <section class="card card--back" aria-label="Card back">
    <div class="wordmark"><span class="wordmark__dot"></span>R7M Horizon</div>
  </section>

  <section class="card card--front" aria-label="Card front">
    <div class="wordmark"><span class="wordmark__dot"></span>R7M Horizon</div>

    <div class="owner">
      <p class="owner__name">Darren Paltrow</p>
      <p class="owner__title">Business Development Manager</p>
    </div>

    <ul class="contacts">
      <li>
        <svg viewBox="0 0 18 18" aria-hidden="true"><rect x="1" y="1" width="16" height="16" rx="2" fill="none" stroke="var(--brand-blue)" stroke-width="1.6"/><path d="M6 4.5c-1 .8-1 2.5.5 4.7s3.3 3.7 4.7 3.8c.8 0 1.3-.6 1.6-1.1l-1.7-1.4-1 .7c-.8-.3-2.2-1.7-2.6-2.6l.7-1-1.4-1.8z" fill="var(--brand-blue)"/></svg>
        +64 (0) 22 4870 619
      </li>
      <li>
        <svg viewBox="0 0 18 18" aria-hidden="true"><rect x="1" y="4" width="16" height="11" fill="var(--brand-blue)"/><path d="M1.5 4.5 9 10l7.5-5.5" fill="none" stroke="#fff" stroke-width="1.4"/></svg>
        darrenp@r7mhorizon.nz
      </li>
      <li>
        <svg viewBox="0 0 18 18" aria-hidden="true"><circle cx="9" cy="9" r="7.5" fill="var(--brand-blue)"/><g fill="none" stroke="#fff" stroke-width="1"><ellipse cx="9" cy="9" rx="3.2" ry="7.5"/><path d="M1.5 9h15M2.8 5h12.4M2.8 13h12.4M9 1.5v15"/></g></svg>
        <span>www.<span class="domain">r7mhorizon.nz</span></span>
      </li>
    </ul>

    <span class="rule-thin"></span>
    <p class="slogan">The best of both worlds</p>
    <span class="rule-band"></span>
  </section>
</main>
</body>
</html>
```